Business is called "Keel Ledger". Accounting and tax services.

I need a flyer for my new business "Keel Ledger". I am an individual accountant working for himself on the Sunshine Coast in Queensland Australia. I would like to see designs that communicate reliability and trust. I believe my point of difference is that I am always available to my clients and I will cap my number of clients to ensure I can service them properly. Accountants in general seem to have a bad reputation for not responding to clients in a timely fashion, whether by email or phone. This is where I intend to differentiate myself. I have included my business card for ideas on colour and for contact information. I have also included some logo's that should go on the flyer. With the RFN logo, the words "Keel Ledger is a RFN Business" needs to be written either above, below or to the right hand side (as per the business card).

Target Market(s)

Small business owners and individuals requiring taxation and financials

Industry/Entity Type

Public Accounting

Font styles to use
Serif

Requirements
Must have
• Supplied logo's, accounting style pictures etc
Services: Small Business Taxation
Company & Trust Tax Returns
Rental Property Returns
Capital Gains Tax
Individual Tax Returns
BAS and IAS lodgements
Nice to have
• Needs to convey a sense of being reliable and responds to clients quickly.
Should not have
• My name

```html
<!DOCTYPE html>
<html lang="en">
<head>
<meta charset="utf-8">
<title>Keel Ledger – Taxation and Business Accountant</title>
<link rel="stylesheet" href="https://fonts.googleapis.com/css2?family=Bitter:ital,wght@0,400;0,500;0,600;1,800&display=swap">
<style>
  :root {
    --green: #21a784;
    --green-text: #1f9f7c;
    --grey: #939598;
    --ink: #1d1d1f;
    --white: #ffffff;
    --teal-soft: #bfe3e6;
    --teal-mid: #6cc3c4;
    --sun-soft: #fde6b0;
    --orange-soft: #f9c98a;
    --floor: #dcf0f7;
    --badge-blue: #1c5aa8;
    --badge-yellow: #f7d117;
    --badge-lime: #b7d53a;
    --badge-sky: #1ab4e8;
  }
  * { margin: 0; padding: 0; box-sizing: border-box; }
  html, body { width: 969px; height: 1200px; overflow: hidden; background: var(--white); }
  .flyer {
    position: relative; width: 969px; height: 1200px; overflow: hidden;
    background: var(--white); font-family: "Bitter", Georgia, serif; color: var(--ink);
  }
  .shapes { position: absolute; inset: 0; }
  .hero-art {
    position: absolute; left: 70px; top: 70px; width: 830px; height: 520px;
    border-radius: 46% 46% 40% 40% / 30% 30% 22% 22%;
    background:
      radial-gradient(ellipse 55% 22% at 50% 92%, var(--floor) 0%, rgba(220,240,247,0) 100%),
      radial-gradient(ellipse 30% 40% at 22% 55%, var(--teal-mid) 0%, rgba(108,195,196,0) 100%),
      radial-gradient(ellipse 28% 45% at 50% 40%, var(--teal-soft) 0%, rgba(191,227,230,0) 100%),
      radial-gradient(ellipse 22% 30% at 40% 78%, var(--sun-soft) 0%, rgba(253,230,176,0) 100%),
      radial-gradient(ellipse 20% 28% at 62% 80%, var(--orange-soft) 0%, rgba(249,201,138,0) 100%),
      radial-gradient(ellipse 22% 35% at 82% 42%, var(--teal-soft) 0%, rgba(191,227,230,0) 100%),
      #f4fafb;
  }
  .headline {
    position: absolute; left: 0; right: 0; top: 598px; text-align: center;
    font-size: 43px; font-weight: 800; font-style: italic; letter-spacing: -0.3px;
  }
  .divider {
    position: absolute; left: 62px; top: 681px; width: 838px; height: 4px;
    background: linear-gradient(90deg, rgba(0,0,0,0), #333 50%, rgba(0,0,0,0));
  }
  .brand { position: absolute; left: 70px; top: 705px; width: 340px; text-align: center; }
  .brand-dot {
    display: block; margin: 0 auto; width: 98px; height: 98px;
    border: 3px solid var(--ink); border-radius: 50%;
  }
  .brand-name {
    margin-top: 24px; font-size: 33px; font-weight: 500; letter-spacing: 10px; text-transform: uppercase;
  }
  .membership { position: absolute; left: 79px; top: 931px; display: flex; align-items: center; gap: 10px; }
  .membership-badge { width: 183px; height: 77px; display: flex; }
  .membership-badge .blue { flex: 0 0 110px; background: var(--badge-blue); }
  .membership-badge .yellow { flex: 1; background: var(--badge-yellow); }
  .membership-note { font-size: 16px; font-weight: 500; line-height: 21px; }
  .tax-agent { position: absolute; left: 74px; top: 1060px; font-size: 11px; line-height: 13px; }
  .services { position: absolute; left: 478px; top: 718px; list-style: none; }
  .services li {
    position: relative; padding-left: 27px; font-size: 25px; font-weight: 500;
    line-height: 36.5px; color: var(--green-text);
  }
  .services li::before {
    content: ""; position: absolute; left: 0; top: 14px; width: 11px; height: 11px;
    border-radius: 50%; background: var(--green-text);
  }
  .contact { position: absolute; right: 58px; top: 1053px; list-style: none; text-align: right; }
  .contact li {
    display: flex; align-items: center; justify-content: flex-end; gap: 8px;
    font-size: 26px; font-weight: 600; line-height: 37px; color: var(--white);
  }
  .contact svg { width: 22px; height: 22px; flex: none; }
</style>
</head>
<body>
<main class="flyer">
  <svg class="shapes" width="969" height="1200" viewBox="0 0 969 1200" aria-hidden="true">
    <path fill="var(--green)" d="M0 0 H444 C400 40 380 80 330 110 C260 150 200 140 150 170 C90 200 40 215 0 260 Z"/>
    <path fill="var(--grey)" d="M640 0 H969 V200 C940 150 900 110 840 95 C760 75 700 60 640 0 Z"/>
    <path fill="var(--green)" d="M239 1200 C300 1120 380 1100 460 1080 C560 1055 600 990 720 985 C820 980 900 960 969 880 L969 1200 Z"/>
    <circle cx="189" cy="1073" r="51" fill="var(--white)" stroke="#555" stroke-width="2"/>
    <circle cx="189" cy="1073" r="30" fill="var(--badge-lime)"/>
    <circle cx="303" cy="1073" r="51" fill="var(--badge-sky)"/>
  </svg>

  <div class="hero-art" role="img" aria-label="Illustration of accountants working with a calculator, a tax form clipboard, coin stacks, a calendar, a wall clock and charts"></div>

  <h1 class="headline">Taxation and Business Accountant</h1>
  <div class="divider"></div>

  <div class="brand">
    <span class="brand-dot"></span>
    <p class="brand-name">Keel Ledger</p>
  </div>

  <div class="membership">
    <div class="membership-badge" role="img" aria-label="RFN membership badge"><span class="blue"></span><span class="yellow"></span></div>
    <p class="membership-note">Keel Ledger<br>is a RFN<br>Business</p>
  </div>

  <p class="tax-agent">Tax agent<br>24681357</p>

  <ul class="services">
    <li>Small Business Taxation</li>
    <li>Company &amp; Trust Tax Returns</li>
    <li>Rental Property Returns</li>
    <li>Capital Gains Tax</li>
    <li>Individual Tax Returns</li>
    <li>BAS and IAS lodgements</li>
  </ul>

  <ul class="contact">
    <li>0412 555 018
      <svg viewBox="0 0 24 24" fill="none" stroke="#fff" stroke-width="2"><path d="M5 3h4l2 5-2.5 1.5a11 11 0 0 0 6 6L16 13l5 2v4a2 2 0 0 1-2 2A16 16 0 0 1 3 5a2 2 0 0 1 2-2z"/></svg>
    </li>
    <li>hello@keelledger.com.au
      <svg viewBox="0 0 24 24" fill="none" stroke="#fff" stroke-width="2"><path d="M3 10l9-7 9 7v10H3z"/><path d="M3 10l9 6 9-6"/></svg>
    </li>
    <li>www.keelledger.com.au
      <svg viewBox="0 0 24 24" fill="none" stroke="#fff" stroke-width="2"><circle cx="12" cy="12" r="9"/><path d="M3 12h18M12 3c3 3 3 15 0 18M12 3c-3 3-3 15 0 18"/></svg>
    </li>
  </ul>
</main>
</body>
</html>
```